Corvexa Background Design

Need to develop a Corvexa Background picture for my profile. The components I want in there are:
1) Name: Abhrajit Dutta
2) Key Skills: Strategy, Innovation, Execution, Growth and Leadership
3) A photograph (an action photograph) The attached photograph is an example.
A black background would be ideal.

The design should meet the Corvexa background size requirements.

The background should reinforce an image of a thinking person but equally capable of implementing.

Leadership

```html
<!DOCTYPE html>
<html lang="en">
<head>
<meta charset="utf-8">
<title>Abhrajit Dutta — Corvexa Background Options</title>
<link href="https://fonts.googleapis.com/css2?family=Open+Sans:wght@400;600;700&family=Itim&display=swap" rel="stylesheet">
<style>
  :root {
    --ink: #000;
    --paper: #fff;
    --word-1: #3a3a3a;
    --word-2: #555;
    --word-3: #777;
    --word-4: #999;
    --word-big: #888;
    --bar-shadow: #4a4a4a;
    --photo-dark: #1c1c1c;
    --photo-light: #6a6a6a;
  }
  * { margin: 0; padding: 0; box-sizing: border-box; }
  html, body { width: 874px; height: 1200px; overflow: hidden; background: var(--paper); }
  body { font-family: "Open Sans", Arial, sans-serif; position: relative; }

  .banner { position: absolute; left: 0; width: 874px; height: 294px; background: var(--ink); overflow: hidden; }
  .banner--words { top: 0; }
  .banner--mirrored { top: 302px; }
  .banner--handwritten { top: 604px; }
  .banner--steps { top: 906px; }

  .portrait {
    position: absolute;
    background: radial-gradient(ellipse at 50% 35%, var(--photo-light), var(--photo-dark) 75%);
  }

  .name {
    position: absolute;
    color: var(--paper);
    font-weight: 700;
    font-size: 56px;
    letter-spacing: -1px;
    line-height: 1;
    white-space: nowrap;
  }

  /* Banner 1: word wall */
  .word-wall { position: absolute; inset: 0; padding-top: 4px; }
  .word-row { white-space: nowrap; font-size: 40px; line-height: 56px; color: var(--word-2); }
  .word-row span { margin-right: 22px; }
  .w1 { color: var(--word-1); } .w2 { color: var(--word-2); } .w3 { color: var(--word-3); } .w4 { color: var(--word-4); }
  .w-big { font-size: 54px; color: var(--word-big); }
  .banner--words .portrait { left: 118px; top: 0; width: 300px; height: 240px; }
  .banner--words .name { left: 112px; top: 222px; }

  /* Banner 2: mirrored skills */
  .skill-stack { position: absolute; list-style: none; color: var(--paper); }
  .skill-stack--mirrored { left: 20px; top: 20px; transform: scaleX(-1); font-family: "Itim", cursive; font-size: 40px; line-height: 50px; width: 270px; text-align: right; }
  .banner--mirrored .portrait { left: 405px; top: 8px; width: 290px; height: 230px; }
  .banner--mirrored .name { right: 24px; top: 222px; }

  /* Banner 3: handwritten skills */
  .skill-stack--hand { left: 30px; top: 20px; font-family: "Itim", cursive; font-size: 40px; line-height: 50px; }
  .banner--handwritten .portrait { left: 405px; top: 8px; width: 290px; height: 230px; }
  .banner--handwritten .name { right: 24px; top: 222px; }

  /* Banner 4: stepped bars */
  .banner--steps .portrait { left: 112px; top: 10px; width: 250px; height: 220px; }
  .banner--steps .name { left: 20px; top: 224px; }
  .step-bars { position: absolute; right: 0; top: 36px; list-style: none; }
  .step-bar {
    height: 46px; margin-bottom: 6px; background: var(--paper); color: var(--ink);
    font-size: 32px; line-height: 46px; text-align: center;
    box-shadow: -12px 0 0 var(--bar-shadow);
    margin-left: auto;
  }
  .step-bar:nth-child(1) { width: 210px; }
  .step-bar:nth-child(2) { width: 238px; }
  .step-bar:nth-child(3) { width: 266px; }
  .step-bar:nth-child(4) { width: 294px; }
  .step-bar:nth-child(5) { width: 322px; }
</style>
</head>
<body>

<section class="banner banner--words">
  <div class="word-wall" aria-hidden="true">
    <div class="word-row"><span class="w-big">strategy</span><span class="w2">leadership</span><span class="w3">growth</span><span class="w2">execution</span></div>
    <div class="word-row"><span class="w1">strategy</span><span class="w3">innovation</span><span class="w2">strategy</span><span class="w4">leadership</span><span class="w2">growth</span></div>
    <div class="word-row"><span class="w2">leadership</span><span class="w1">strategy</span><span class="w-big">execution</span><span class="w3">innovation</span><span class="w2">strategy</span></div>
    <div class="word-row"><span class="w1">tion</span><span class="w2">strategy</span><span class="w3">innovation</span><span class="w-big">growth</span><span class="w2">execution</span></div>
    <div class="word-row"><span class="w1">growth</span><span class="w1">execution</span><span class="w2">strategy</span><span class="w1">innovation</span><span class="w-big">leadership</span></div>
  </div>
  <div class="portrait" role="img" aria-label="Action photograph of Abhrajit Dutta pointing upward"></div>
  <h1 class="name">Abhrajit DUTTA</h1>
</section>

<section class="banner banner--mirrored">
  <ul class="skill-stack skill-stack--mirrored">
    <li>strategy</li><li>execution</li><li>innovation</li><li>growth</li><li>leadership</li>
  </ul>
  <div class="portrait" role="img" aria-label="Action photograph of Abhrajit Dutta pointing upward"></div>
  <h2 class="name">Abhrajit DUTTA</h2>
</section>

<section class="banner banner--handwritten">
  <ul class="skill-stack skill-stack--hand">
    <li>strategy</li><li>execution</li><li>innovation</li><li>growth</li><li>leadership</li>
  </ul>
  <div class="portrait" role="img" aria-label="Action photograph of Abhrajit Dutta pointing upward"></div>
  <h2 class="name">Abhrajit DUTTA</h2>
</section>

<section class="banner banner--steps">
  <div class="portrait" role="img" aria-label="Action photograph of Abhrajit Dutta pointing upward"></div>
  <h2 class="name">Abhrajit DUTTA</h2>
  <ul class="step-bars">
    <li class="step-bar">strategy</li>
    <li class="step-bar">execution</li>
    <li class="step-bar">innovation</li>
    <li class="step-bar">growth</li>
    <li class="step-bar">leadership</li>
  </ul>
</section>

</body>
</html>
```